Letterhead, business card and envelop package design for Morvaly

Business to Business
Training
Distrbution of some products
Services.

We partner with companies to work with us on our products. We are based in USA but have international partners all over the world.

```html
<!DOCTYPE html>
<html lang="en">
<head>
<meta charset="utf-8">
<title>Morvaly Letterhead</title>
<link rel="stylesheet" href="https://fonts.googleapis.com/css2?family=Open+Sans:wght@400;600;700&family=Questrial&display=swap">
<style>
  :root {
    --backdrop: #8c8c8c;
    --paper: #ffffff;
    --brand-green: #6cb52d;
    --map-tint: #e6f0dc;
    --ink: #1e1e1e;
    --rule: #9a9a9a;
    --accent-orange: #f3901d;
    --accent-blue: #2aa3dc;
  }
  * { margin: 0; padding: 0; box-sizing: border-box; }
  html, body { width: 959px; height: 1200px; overflow: hidden; background: var(--backdrop); }
  .letterhead {
    position: absolute; left: 24px; top: 0; width: 876px; height: 1150px;
    background: var(--paper);
    box-shadow: 6px 6px 14px rgba(0,0,0,0.35);
    font-family: "Questrial", sans-serif; color: var(--ink);
  }
  .header-map {
    position: absolute; left: 500px; top: 0; width: 376px; height: 170px;
    background: radial-gradient(ellipse at 55% 40%, var(--map-tint) 0%, rgba(230,240,220,0.4) 55%, rgba(255,255,255,0) 80%);
  }
  .brand {
    position: absolute; left: 50px; top: 70px;
    display: flex; flex-direction: column; align-items: flex-start; gap: 26px;
  }
  .brand-mark { width: 24px; height: 24px; background: var(--brand-green); }
  .brand-name {
    font-family: "Open Sans", sans-serif; font-weight: 700; font-size: 38px;
    color: var(--brand-green); letter-spacing: -1px; line-height: 1;
  }
  .contact {
    position: absolute; left: 232px; top: 106px;
    font-family: "Open Sans", sans-serif; font-size: 12px; line-height: 14px; color: #222;
  }
  .contact .line { font-weight: 600; }
  .contact .web { margin-top: 4px; color: var(--brand-green); font-weight: 600; }
  .header-rule {
    position: absolute; left: 232px; top: 178px; width: 594px; height: 1px; background: var(--rule);
  }
  .letter {
    position: absolute; left: 88px; top: 286px; width: 690px;
    font-size: 13px; line-height: 18px;
  }
  .letter p { margin-bottom: 16px; }
  .closing { margin-top: 4px; }
  .footer-band {
    position: absolute; left: 0; top: 1116px; width: 876px; height: 12px;
    background: linear-gradient(90deg, var(--brand-green) 0%, var(--brand-green) 50%, var(--accent-orange) 72%, var(--accent-blue) 100%);
  }
</style>
</head>
<body>
<div class="letterhead">
  <div class="header-map" role="img" aria-label="Faint world map decoration"></div>

  <div class="brand">
    <div class="brand-mark"></div>
    <div class="brand-name">Morvaly</div>
  </div>

  <div class="contact">
    <div class="line">Address line - Address Line - Address Line</div>
    <div class="line">Mobile: 0123-400-5551020 Fax: 0123-400-5551020</div>
    <div class="line">Email: hello@morvaly.com</div>
    <div class="web">www.morvaly.com</div>
  </div>
  <div class="header-rule"></div>

  <div class="letter">
    <p>September 24, 2012</p>
    <p>Full Name<br>12345 Address<br>Address Line - Address line</p>
    <p>Dear Ms. ABCD,</p>
    <p>Text Text Text Text Text Text Text Text Text Text Text Text Text Text Text Text Text Text Text Text Text Text Text Text Text Text Text Text Text Text Text Text Text Text Text Text Text Text Text Text Text Text Text Text Text Text Text Text Text Text Text Text Text Text Text Text Text Text Text Text Text Text Text Text Text Text Text Text.</p>
    <p>Text Text Text Text Text Text Text Text Text Text Text Text Text Text Text Text Text Text Text Text Text Text Text Text Text Text Text Text Text Text Text Text Text Text Text Text Text Text Text Text Text Text Text Text Text Text Text Text Text Text Text Text Text Text Text Text Text Text Text Text Text Text Text Text Text Text Text Text Text Text Text Text Text Text Text Text Text Text Text Text Text Text Text Text Text Text Text Text Text Text Text.</p>
    <p>Text Text Text Text Text Text Text Text Text Text Text Text Text Text Text Text Text Text Text Text Text Text Text Text Text Text Text Text Text Text Text Text Text Text Text Text Text Text Text Text Text Text Text Text Text Text Text Text Text Text Text Text Text Text Text.</p>
    <p>Text Text Text Text Text Text Text Text Text Text Text.</p>
    <p class="closing">Sincerely</p>
    <p>Full Name<br>Designation</p>
  </div>

  <div class="footer-band" role="img" aria-label="Multicolour footer band in the brand tones"></div>
</div>
</body>
</html>
```